Tellmora Corporate Stationery

Look for design of all new corporate stationery for an existing insurance broking business that is going through a redesign and move from older partners to younger family members. New Logo is attached. Company is Brisbane based.
Colours in the Logo is Hex #43bed8 and website features a lot of hex #17b8d8. Website front page "A plan to protect you" - headline. "Professional and Individual advice to protect your greatest assets" - tagline.

Stationery required: Business Cards, Letter head, Thank-you cards, Birthday cards, Presentation folders, With Compliment slips and a powerpoint template. We also would like to send a card to all customers with the something along of the lines of "something new".

Target Market(s)

Customers of Insurance business looking at superannuation, life and income protection insurance, investment advice and wills

Industry/Entity Type

Insurance Broker

Font styles to use
Other font styles liked:
• same as logo

Requirements
Must have
• The above designs for new stationery for the new business including:
• Business Cards, Letter head, Thank-you cards, Birthday cards, Presentation folders, With Compliment slips and a powerpoint template. We also would like to send a card to all customers with the something along of the lines of "something new".
Nice to have
• It is a new look - long time family business being passed to next generation - big focus on advice for YOU, individual advice etc..

```html
<!DOCTYPE html>
<html lang="en">
<head>
<meta charset="utf-8">
<title>Tellmora Business Card</title>
<link href="https://fonts.googleapis.com/css2?family=Open+Sans:wght@400;600&display=swap" rel="stylesheet">
<style>
  :root {
    --brand: #3bbcd9;
    --brand-deep: #17b8d8;
    --grey: #8a8d91;
    --grey-light: #c9cacc;
    --ink: #6d7075;
    --paper: #ffffff;
    --backdrop: #e9ebed;
  }
  * { box-sizing: border-box; margin: 0; padding: 0; }
  html, body {
    width: 1200px; height: 950px; overflow: hidden;
    background: var(--backdrop);
    font-family: "Open Sans", Arial, sans-serif;
  }
  .card {
    position: absolute;
    width: 720px; height: 410px;
    border-radius: 4px;
    overflow: hidden;
    box-shadow: 0 8px 24px rgba(0,0,0,0.18);
  }
  .card--front { left: 60px; top: 50px; background: var(--paper); }
  .card--back { left: 420px; top: 500px; background: var(--brand); }

  .front-wave { position: absolute; inset: 0; }

  .brand-name {
    position: absolute;
    font-weight: 600;
    color: var(--brand);
    letter-spacing: 1px;
    text-transform: uppercase;
    display: flex; align-items: center; gap: 14px;
  }
  .brand-name .dot {
    width: 30px; height: 30px; border-radius: 50%;
    background: var(--grey);
  }
  .card--front .brand-name { left: 70px; top: 150px; font-size: 40px; }

  .contact {
    position: absolute; left: 360px; top: 40px;
    padding-left: 32px;
    border-left: 1px solid #e2e3e5;
    height: 200px;
  }
  .contact__name {
    color: var(--brand); font-weight: 600; font-size: 22px;
    letter-spacing: 0.5px; text-transform: uppercase;
  }
  .contact__role {
    color: var(--grey); font-size: 13px; text-transform: uppercase;
    margin-bottom: 14px;
  }
  .contact__address { color: var(--ink); font-size: 13px; line-height: 1.45; margin-bottom: 8px; }
  .contact__list { list-style: none; }
  .contact__list li {
    display: flex; align-items: center; gap: 10px;
    color: var(--ink); font-size: 13px; line-height: 21px;
  }
  .contact__list svg { width: 13px; height: 13px; fill: var(--brand); flex: none; }

  .card--back .brand-name {
    left: 60px; top: 160px; font-size: 48px; color: var(--paper);
  }
  .card--back .brand-name .dot { background: var(--paper); width: 36px; height: 36px; }
  .back-web {
    position: absolute; left: 110px; top: 228px;
    color: var(--paper); font-size: 15px; letter-spacing: 3px;
  }
</style>
</head>
<body>

<section class="card card--front">
  <svg class="front-wave" viewBox="0 0 720 410" preserveAspectRatio="none" aria-hidden="true">
    <path d="M0 330 C 220 330, 480 300, 720 200 L720 410 L0 410 Z" fill="var(--grey-light)"/>
    <path d="M0 344 C 230 344, 490 314, 720 216 L720 410 L0 410 Z" fill="var(--brand)"/>
  </svg>

  <div class="brand-name"><span class="dot"></span>Tellmora</div>

  <div class="contact">
    <p class="contact__name">Daniel Hart</p>
    <p class="contact__role">CEO/Founder</p>
    <p class="contact__address">4120 Wattle Street<br>Brisbane, QLD 4000</p>
    <ul class="contact__list">
      <li><svg viewBox="0 0 16 16"><path d="M3 1h3l1.5 4-2 1.2a9 9 0 0 0 4.3 4.3L11 8.5l4 1.5v3a2 2 0 0 1-2 2A13 13 0 0 1 1 3a2 2 0 0 1 2-2z"/></svg>07 3184 2260</li>
      <li><svg viewBox="0 0 16 16"><path d="M4 0h8a1 1 0 0 1 1 1v14a1 1 0 0 1-1 1H4a1 1 0 0 1-1-1V1a1 1 0 0 1 1-1zm1 2v10h6V2z"/></svg>0412 587 903</li>
      <li><svg viewBox="0 0 16 16"><path d="M4 0h7v4H4zM1 5h14v8h-3v3H4v-3H1zm5 6v3h4v-3z"/></svg>07 3184 2261</li>
      <li><svg viewBox="0 0 16 16"><path d="M0 3h16v10H0zm1.5 1.2L8 9l6.5-4.8V4h-13z"/></svg>dan@tellmora.com</li>
      <li><svg viewBox="0 0 16 16"><circle cx="8" cy="8" r="8"/></svg>www.tellmora.com</li>
    </ul>
  </div>
</section>

<section class="card card--back">
  <div class="brand-name"><span class="dot"></span>Tellmora</div>
  <p class="back-web">www.tellmora.com</p>
</section>

</body>
</html>
```